The design should look similar to the uploaded example to accommodate the information needed for a business card template. I would like to see the colors orange and charcoal grey incorporated along with the logo.The following should be on the back of the card SPECIALIZING IN NEW AND USED TIRES & WHEELS FOR:- Loaders- Skid Steers- Telehandlers- Boom Lifts- Forklifs and moreELIMINATING DOWNTIMEWheel Exchange Program for New & Used Foam Filled and Solid Rubber TiresSPECIALTY SERVICES- Foam Filling Tires- Largest Tire Press in SE- ONSITE Forklift Tire Press- Boom Truck Services - Rubber Tracks

Target Market(s)

New and Existing Customers

Industry/Entity Type

Business

Contact Information for Business Card

NAMEHEAVY DUTY TIRE, LLC8470 Belvedere RoadWest Palm Beach, FL 33411P: 844-HD-TIRESF: 561-431-6469C:E: W: WWW.GRANITERIMSUPPLY-EXAMPLE.COM

Font styles to use
Sans Serif

Colors
f37122
333333

Requirements
Must have
• The logo and the information indicated for the backside of the card
Nice to have
• Keep the orange and charcoal grey colors

```html
<!DOCTYPE html>
<html lang="en">
<head>
<meta charset="utf-8">
<title>Granite Rim Supply Business Card</title>
<link href="https://fonts.googleapis.com/css2?family=Source+Sans+3:wght@400;600;700&display=swap" rel="stylesheet">
<style>
  :root{
    --orange:#f37122;
    --orange-soft:#f68a45;
    --charcoal:#333333;
    --card:#ffffff;
    --backdrop:#121212;
    --faint:rgba(51,51,51,0.06);
    --faint-orange:rgba(243,113,34,0.07);
  }
  *{margin:0;padding:0;box-sizing:border-box}
  html,body{width:1200px;height:900px;overflow:hidden}
  body{background:var(--backdrop);font-family:"Source Sans 3",Arial,sans-serif;color:var(--charcoal);position:relative}
  .card{position:absolute;top:170px;width:347px;height:561px;background:var(--card);overflow:hidden}
  .card--front{left:259px}
  .card--back{left:631px;text-align:center}
  .band{position:absolute;left:101px;width:144px;background:var(--orange-soft)}
  .band--top{top:0;height:30px}
  .band--bottom{bottom:0;height:28px}
  .brand-mark{position:absolute;left:0;right:0;top:81px;height:146px;display:flex;align-items:center;justify-content:center;gap:9px}
  .brand-dot{width:16px;height:16px;border-radius:50%;background:var(--orange);flex:none}
  .brand-name{font-weight:700;font-size:28px;line-height:1.05;color:var(--charcoal);text-align:left}
  .front-text{position:absolute;left:0;right:0;text-align:center}
  .person-name{top:245px;font-size:21px;font-weight:600;color:var(--orange)}
  .company{top:285px;font-size:17px;font-weight:600;color:var(--orange)}
  .address{top:311px;font-size:15.5px;line-height:24px}
  .contacts{top:370px;list-style:none;font-size:15.5px;line-height:23px}
  .contacts li{display:flex;align-items:center;justify-content:center;gap:8px}
  .contacts svg{width:11px;height:11px;fill:var(--orange);flex:none}
  .watermark{position:absolute;left:12px;top:70px;width:325px;height:325px;border-radius:50%;background:var(--faint-orange);display:flex;align-items:center;justify-content:center}
  .watermark span{font-weight:700;font-size:58px;line-height:1;color:var(--faint)}
  .back-content{position:relative}
  .heading{font-size:17.5px;font-weight:600;color:var(--orange);text-transform:uppercase;line-height:23px}
  .heading--lead{padding-top:85px}
  .heading--small{font-size:15.5px;line-height:20px}
  .heading--section{font-size:20px;margin-top:40px}
  .equipment{list-style:none;display:flex;flex-wrap:wrap;justify-content:center;column-gap:20px;font-size:16.5px;font-weight:600;line-height:23px;margin:20px 12px 0}
  .bullet::before{content:"";display:inline-block;width:5px;height:5px;background:var(--orange);margin-right:4px;vertical-align:middle}
  .downtime{margin-top:48px}
  .program{font-size:16.5px;font-weight:600;line-height:21px}
  .services{list-style:none;font-size:16.5px;font-weight:600;line-height:23px;margin-top:32px}
</style>
</head>
<body>
  <section class="card card--front">
    <div class="band band--top"></div>
    <div class="brand-mark"><span class="brand-dot"></span><span class="brand-name">GRANITE<br>RIM</span></div>
    <p class="front-text person-name">Marcus Delaney</p>
    <p class="front-text company">GRANITE RIM SUPPLY, LLC</p>
    <p class="front-text address">5126 Marston Lane<br>Harbor Grove, FL 33470</p>
    <ul class="front-text contacts">
      <li><svg viewBox="0 0 12 12"><path d="M2.5 0.8l2 2-1 1.4c.7 1.5 1.8 2.6 3.3 3.3l1.4-1 2 2-1.3 1.9C5 10 1.9 6.9 0.6 2.1z"/></svg>844-GR-WHEEL</li>
      <li><svg viewBox="0 0 12 12"><path d="M1 4h10v7H1zM3 1h6v2H3z"/></svg>561-278-9053</li>
      <li><svg viewBox="0 0 12 12"><path d="M3 0h6v12H3zM4 1.5v8h4v-8z" fill-rule="evenodd"/></svg>555-014-2290</li>
      <li><svg viewBox="0 0 12 12"><path d="M0 2h12v8H0zM1 3l5 3.5L11 3z" fill-rule="evenodd"/></svg>info@graniterim-example.com</li>
      <li><svg viewBox="0 0 12 12"><circle cx="6" cy="6" r="6"/></svg>www.graniterimsupply-example.com</li>
    </ul>
    <div class="band band--bottom"></div>
  </section>

  <section class="card card--back">
    <div class="watermark"><span>GRANITE<br>RIM</span></div>
    <div class="back-content">
      <h2 class="heading heading--lead">Specializing in new and used tires<br>&amp; wheels for</h2>
      <ul class="equipment">
        <li class="bullet">Loaders</li>
        <li class="bullet">Skid Steers</li>
        <li class="bullet">Telehandlers</li>
        <li class="bullet">Boom Lifts</li>
        <li class="bullet">Forklifs and more</li>
      </ul>
      <h3 class="heading heading--small downtime">Eliminating Downtime</h3>
      <p class="program">Wheel Exchange Program for New &amp;<br>Used Foam Filled and Solid Rubber Tires</p>
      <h2 class="heading heading--section">Specialty Services</h2>
      <ul class="services">
        <li class="bullet">Foam Filling Tires</li>
        <li class="bullet">Largest Tire Press in SE</li>
        <li class="bullet">ONSITE Forklift Tire Press</li>
        <li class="bullet">Boom Truck Services</li>
        <li class="bullet">Rubber Tracks</li>
      </ul>
    </div>
  </section>
</body>
</html>
```